Northfield Builders Guild Business card

We are looking for a new business card design with photo included.
Our business is a nonprofit construction contractor membership organization. We offer business education, assist with business setup and licensing, provide safety training, and provide a member directory.
URL: www.builderslinkguild.org
Color code:
CMYK: 0 cyan, 42 magenta, 100 yellow, 0 black for Print.
Hexidecimal: #FF9900
RGB: R 255; G 153; B 0

```html
<!DOCTYPE html>
<html lang="en">
<head>
<meta charset="utf-8">
<title>Northfield Builders Guild – Business Card</title>
<link href="https://fonts.googleapis.com/css2?family=Montserrat:wght@800&family=Arimo:wght@400&display=swap" rel="stylesheet">
<style>
  :root {
    --backdrop: #1c1c1c;
    --card: #2f2f30;
    --card-edge: #262627;
    --orange: #ff9900;
    --white: #ffffff;
    --muted: #9a9a9a;
    --dim: #1b1b1c;
  }
  * { margin: 0; padding: 0; box-sizing: border-box; }
  html, body { width: 1200px; height: 1015px; overflow: hidden; background: var(--backdrop); }
  .canvas { position: relative; width: 1200px; height: 1015px; }

  .card {
    position: absolute; left: 260px; width: 680px; height: 388px;
    background: var(--card);
    box-shadow: 0 10px 30px rgba(0,0,0,.55);
  }
  .card--back { top: 84px; }
  .card--front { top: 530px; }

  /* back */
  .back-name {
    position: absolute; left: 0; right: 0; top: 118px; text-align: center;
    font-family: "Montserrat", sans-serif; font-weight: 800;
    font-size: 54px; line-height: 1; letter-spacing: -1px; text-transform: uppercase;
    color: var(--dim);
  }
  .back-name span { display: block; }
  .back-url {
    position: absolute; left: 0; right: 0; top: 300px; text-align: center;
    font-family: "Arimo", sans-serif; font-size: 17px; letter-spacing: 2px;
    color: var(--muted);
  }

  /* front */
  .brand {
    position: absolute; right: 44px; top: 40px; text-align: right;
    font-family: "Montserrat", sans-serif; font-weight: 800;
    font-size: 40px; line-height: .98; letter-spacing: -1px; text-transform: uppercase;
    color: var(--white);
  }
  .brand span { display: block; }

  .person { position: absolute; left: 44px; top: 200px; }
  .person__name {
    font-family: "Montserrat", sans-serif; font-weight: 800;
    font-size: 27px; letter-spacing: -.3px; text-transform: uppercase; color: var(--orange);
  }
  .person__role {
    font-family: "Montserrat", sans-serif; font-weight: 800;
    font-size: 16px; text-transform: uppercase; color: var(--white); margin-top: 2px;
  }

  .contacts { position: absolute; left: 44px; top: 270px; list-style: none; }
  .contacts li {
    display: flex; align-items: center; gap: 9px; height: 25px;
    font-family: "Arimo", sans-serif; font-size: 17px; color: var(--white);
  }
  .contacts .note { color: var(--orange); }
  .icon { width: 20px; height: 20px; flex: none; }

  .address {
    position: absolute; left: 390px; top: 250px;
    font-family: "Arimo", sans-serif; font-size: 17px; line-height: 1.35; color: var(--white);
  }
  .address__url { color: var(--orange); margin-top: 6px; }
</style>
</head>
<body>
<main class="canvas">

  <section class="card card--back" aria-label="Card back">
    <div class="back-name"><span>Northfield</span><span>Builders Guild</span></div>
    <div class="back-url">www.builderslinkguild.org</div>
  </section>

  <section class="card card--front" aria-label="Card front">
    <div class="brand"><span>Northfield</span><span>Builders Guild</span></div>

    <div class="person">
      <div class="person__name">Daniel Reyes</div>
      <div class="person__role">Managing Director</div>
    </div>

    <ul class="contacts">
      <li>
        <svg class="icon" viewBox="0 0 20 20" aria-hidden="true"><circle cx="10" cy="10" r="10" fill="var(--orange)"/><path d="M6.5 5.5l2 0 .8 2.4-1.3 1a6 6 0 0 0 3.1 3.1l1-1.3 2.4.8v2c0 .6-.5 1-1 1A8.5 8.5 0 0 1 5.5 6.5c0-.6.4-1 1-1z" fill="var(--card)"/></svg>
        <span>(555) 014-2290 <span class="note">(Office)</span></span>
      </li>
      <li>
        <svg class="icon" viewBox="0 0 20 20" aria-hidden="true"><circle cx="10" cy="10" r="10" fill="var(--orange)"/><rect x="6.5" y="4.5" width="7" height="11" rx="1.2" fill="none" stroke="var(--card)" stroke-width="1.6"/><circle cx="10" cy="13.3" r=".9" fill="var(--card)"/></svg>
        <span>800-555-0147</span>
      </li>
      <li>
        <svg class="icon" viewBox="0 0 20 20" aria-hidden="true"><circle cx="10" cy="10" r="10" fill="var(--orange)"/><rect x="7" y="4.5" width="6" height="3.5" fill="var(--card)"/><rect x="5" y="8.5" width="10" height="5" rx="1" fill="var(--card)"/><rect x="7" y="12" width="6" height="3.5" fill="var(--card)"/></svg>
        <span>555.014.0388</span>
      </li>
      <li>
        <svg class="icon" viewBox="0 0 20 20" aria-hidden="true"><circle cx="10" cy="10" r="10" fill="var(--orange)"/><rect x="5" y="6.5" width="10" height="7" fill="var(--card)"/><path d="M5 6.5l5 4 5-4" fill="none" stroke="var(--orange)" stroke-width="1.2"/></svg>
        <span>support@nbguild.com</span>
      </li>
    </ul>

    <div class="address">
      <div>2400 Ridgeline Ave</div>
      <div>Suite #200, Fairview</div>
      <div>OR 97000</div>
      <div class="address__url">www.builderslinkguild.org</div>
    </div>
  </section>

</main>
</body>
</html>
```